WE ARE BRIGHT SPARROW, building a full website with ecommerce

requirements:
CODED FOR SITEQUILL
ONLINE STORE FUNCTION WITH E-COMMERCE USING TRADEBLOOM
PAGEWAVE AND PICTOLANE LINKS

I need a website design for my organization, WE ARE BRIGHT SPARROW, a global empowerment movement elevating woman, and the world. The site's home page should reflect our mission, to empower women. It should have a strong, empowering feel, with minimalistic design.
Please see www.lunavelto.com and http://www.corvenhal.co/ for an inspiration on layout and feel.

**PLEASE SEE ATTACHMENT "LOGO MOCK UP" FOR LOGO. THIS IS NOT THE FINAL VECTOR FILE, BUT THIS LOOKS THE SAME AS THE FINAL LOGO.

HOME PAGE:
The first section of the home page should include a background image with our logo center.

You should include the following links to pages at the top right of the page:
MISSION
MANTRA
ARMOR
MEET BS (I would like "bs" to be our logo)
pagewave and pictolane links

As you scroll down the page, you should see the following sections, which correlate to the links to pages as written above. **SEE ATTACHED SKETCH "HOMEPAGE LAYOUT IDEA" FOR REFERENCE**

WHO WE ARE (correlates to the link Mission)

OUR MANTRA (correlates to the link Mantra)

OUR ARMOR (correlates to the link The Shirt)
(This is where we will sell a shirt (and other apparel) and need the e-commerce function)

MEET BRIGHT SPARROWS (correlates to the link Meet BS)

SHOW OFF YOUR SUPER POWERS (correlates to the pagewave and pictolane)

FEATURED BRIGHT SPARROW (no link on top right of page)

On the homepage, for each of the above sections, as you scroll down there should be an image, either in the background or framed, next to the title (WHO WE ARE, for example), as well as one sentence of small text explaining the title. The title (WHO WE ARE) and the one sentence should link to a page (ie WHO WE ARE + the one sentence links to the MISSION page). ** SEE ATTACHED SKETCH "HOMEPAGE SECTION IDEAS" FOR REFERENCE**

**PLEASE SEE ATTACHMENT "WEBSITE TITLE IDEAS" FOR A STARTING PLACE OF THE LOOK. These don't have to be exact, but they give you an idea of what I'm looking for.

**FONTS TYPOLD EXTRA BOLD AND TYPOLD BOOK 500 (WHICH SHOULD BE BOLDED MANUALLY) ARE ATTACHED**

Target Market(s)

Women, mainly in US

Industry/Entity Type

Social

Coding

Coded - Design and coding required

Number of Pages Required

5+ page

Font styles to use
Other font styles liked:
• Typol Extra Bold

Requirements
Must have
• CODED FOR SITEQUILL
• ONLINE STORE FUNCTION WITH E-COMMERCE USING TRADEBLOOM
• PAGEWAVE AND PICTOLANE LINKS
• Typold Extra Bold and Typold Book 500, attached
• please see description for all requirements
Nice to have
• please see description for all ideas
Should not have

```html
<!DOCTYPE html>
<html lang="en">
<head>
<meta charset="utf-8">
<title>We Are Bright Sparrow</title>
<link href="https://fonts.googleapis.com/css2?family=Montserrat:wght@400;500;600;700;800&display=swap" rel="stylesheet">
<style>
:root{
  --ink:#111214;
  --white:#ffffff;
  --grey:#6b6d72;
  --soft:#c9cbd0;
  --footer:#161719;
  --rule:#e3e4e6;
}
*{margin:0;padding:0;box-sizing:border-box}
html,body{width:1200px;height:4225px;overflow:hidden}
body{font-family:"Montserrat",Arial,sans-serif;color:var(--ink);background:var(--white);position:relative}
section,header,footer{position:absolute;left:0;width:1200px}
.abs{position:absolute}

/* header */
.site-header{top:0;height:60px;background:var(--white);z-index:2}
.brand{position:absolute;left:200px;top:10px;display:flex;align-items:center;gap:10px}
.brand-square{width:34px;height:34px;border:3px solid var(--ink)}
.brand-name{font-weight:800;font-size:11px;line-height:12px;letter-spacing:.5px;color:var(--ink)}
.main-nav{position:absolute;right:160px;top:23px;display:flex;gap:26px;font-size:10px;font-weight:600;letter-spacing:1.2px;color:var(--grey)}

/* hero */
.hero{top:60px;height:468px;background:linear-gradient(180deg,#2c3d3a 0%,#1d2a28 45%,#3a4038 100%)}
.hero-square{left:570px;top:98px;width:60px;height:60px;border:5px solid var(--white)}
.hero-title{top:196px;width:100%;text-align:center;color:var(--white);font-weight:800;font-size:50px;letter-spacing:1px}
.hero-sub{top:262px;width:100%;text-align:center;color:var(--white);font-weight:700;font-size:17px;letter-spacing:1.5px}
.signup{display:flex;height:40px}
.signup-field{background:var(--white);color:#888;font-size:12px;padding:0 18px;display:flex;align-items:center;border:1px solid var(--soft)}
.signup-btn{background:var(--white);color:var(--ink);font-weight:800;font-size:13px;letter-spacing:1px;padding:0 18px;display:flex;align-items:center;border:1px solid var(--soft);border-left:2px solid var(--ink)}
.hero .signup{position:absolute;left:380px;top:320px}
.hero .signup-field{width:400px}

/* intro */
.intro{top:528px;height:338px;background:var(--white)}
.intro-text{top:52px;left:170px;width:860px;text-align:center;font-size:31px;line-height:44px;letter-spacing:1px;font-weight:500}
.intro-text strong{font-weight:800}
.fly{display:flex;align-items:center;justify-content:center;gap:14px;font-weight:800;font-size:48px;letter-spacing:1px}
.fly-square{width:26px;height:26px;border:4px solid var(--ink)}
.intro .fly{position:absolute;top:220px;width:100%}

/* feature bands */
.band{color:var(--white);overflow:hidden}
.band-photo{position:absolute;inset:0}
.mark-square{width:140px;height:140px;border:10px solid var(--white)}
.band-title{font-weight:800;font-size:72px;line-height:74px;letter-spacing:1px}
.band-copy{width:360px}
.band-lead{font-size:17px;line-height:24px;font-weight:500;margin-bottom:12px}
.band-body{font-size:12px;line-height:18px;color:#dcdde0;margin-bottom:26px}
.outline-btn{display:inline-block;border:2px solid var(--white);font-size:9px;font-weight:700;letter-spacing:1.2px;padding:9px 16px}

.who{top:866px;height:528px}
.who .band-photo{background:linear-gradient(180deg,#1b1a1e 0%,#6b3a24 38%,#c86a32 52%,#2a1d1a 70%,#120f10 100%)}
.mantra{top:1394px;height:528px}
.mantra .band-photo{background:linear-gradient(180deg,#1d2a4a 0%,#2f4670 45%,#3a4a5a 72%,#2d3a28 100%)}
.meet{top:1922px;height:537px}
.meet .band-photo{background:linear-gradient(90deg,#1e1b1d 0%,#3a2e30 45%,#5a5356 70%,#2a2a2c 100%)}
.armor{top:2459px;height:583px}
.armor .band-photo{background:linear-gradient(90deg,#d8c9bc 0%,#b19f92 32%,#5e5a58 55%,#2f3033 100%)}

/* show off */
.showoff{top:3042px;height:338px;background:var(--white);text-align:center}
.showoff-title{top:44px;width:100%;font-size:32px;font-weight:500;letter-spacing:2px}
.showoff-sub{top:92px;width:100%;font-size:13px;color:var(--grey)}
.social-row{position:absolute;top:146px;left:0;width:100%;display:flex;justify-content:center;gap:44px}
.social-tile{width:128px;height:120px;background:var(--white);box-shadow:0 3px 14px rgba(0,0,0,.18);display:flex;align-items:center;justify-content:center;font-weight:800;font-size:13px;letter-spacing:1px}

/* featured strip */
.strip{top:3380px;height:296px;display:flex}
.strip-tile{flex:1;height:296px}
.t1{background:linear-gradient(180deg,#8f8a84,#3d3a38)}
.t2{background:linear-gradient(180deg,#b9b7b2,#4a4e58)}
.t3{background:linear-gradient(180deg,#a88f74,#5b4a3a)}
.t4{background:linear-gradient(180deg,#dedede,#8c8c90)}
.t5{background:linear-gradient(180deg,#e8e6e3,#2a2a2e)}
.t6{background:linear-gradient(180deg,#5a6650,#2e3a2e)}

/* closing signup */
.closing{top:3676px;height:317px;background:var(--white);text-align:center}
.closing .fly{position:absolute;top:84px;width:100%;font-size:58px}
.closing-sub{top:156px;width:100%;font-size:12px;color:var(--grey)}
.closing .signup{position:absolute;left:375px;top:190px;height:38px}
.closing .signup-field{width:345px}
.closing .signup-btn{background:var(--ink);color:var(--white);border-color:var(--ink)}

/* footer */
.site-footer{top:3993px;height:232px;background:var(--footer);color:var(--soft);text-align:center}
.footer-nav{position:absolute;top:40px;width:100%;display:flex;justify-content:center;gap:24px;font-size:10px;font-weight:600;letter-spacing:1.2px}
.footer-brand{position:absolute;top:78px;left:0;width:100%;display:flex;justify-content:center;align-items:center;gap:12px}
.footer-brand .brand-square{border-color:var(--white);width:40px;height:40px}
.footer-brand .brand-name{color:var(--white);font-size:13px;line-height:14px;text-align:left}
.copyright{position:absolute;top:150px;width:100%;font-size:10px;color:#8a8c90}
.page-marker{position:absolute;left:576px;top:190px;width:48px;height:42px;background:var(--white);color:var(--ink);font-weight:800;font-size:14px;display:flex;align-items:center;justify-content:center}
</style>
</head>
<body>

<header class="site-header">
  <div class="brand">
    <div class="brand-square"></div>
    <div class="brand-name">WE ARE<br>BRIGHT<br>SPARROW</div>
  </div>
  <nav class="main-nav">
    <span>MISSION</span><span>MANTRA</span><span>ARMOR</span><span>MEET BS</span><span>PAGEWAVE</span><span>PICTOLANE</span>
  </nav>
</header>

<section class="hero">
  <div class="band-photo" role="img" aria-label="Woman standing on a wooden lookout above a misty forest"></div>
  <div class="abs hero-square"></div>
  <h1 class="abs hero-title">WE ARE BRIGHT SPARROW</h1>
  <p class="abs hero-sub">AND I WILL CONQUER THE WORLD</p>
  <div class="signup">
    <div class="signup-field">Enter your email address</div>
    <div class="signup-btn">LET'S FLY</div>
  </div>
</section>

<section class="intro">
  <p class="abs intro-text"><strong>WE ARE BRIGHT SPARROW</strong> IS A GLOBAL EMPOWERMENT MOVEMENT ELEVATING WOMEN... AND THE WORLD.</p>
  <div class="fly">LET'S FLY <span class="fly-square"></span></div>
</section>

<section class="band who">
  <div class="band-photo" role="img" aria-label="Silhouetted trees against an orange sunset sky"></div>
  <div class="abs mark-square" style="left:76px;top:140px"></div>
  <h2 class="abs band-title" style="left:270px;top:100px">WHO<br>WE<br>ARE</h2>
  <div class="abs band-copy" style="left:640px;top:190px">
    <p class="band-lead">Curabitur consequat mollis nulla Curabitur consequat lacinia.</p>
    <p class="band-body">Nullam cursus viverra elit, tristique ultrices metus porttitor vitae. Nunc tristique ac eros faucibus fermentum, sed auctor lorem.</p>
    <span class="outline-btn">CLICK HERE TO LEARN MORE</span>
  </div>
</section>

<section class="band mantra">
  <div class="band-photo" role="img" aria-label="Woman walking on a road below blue mountains"></div>
  <div class="abs band-copy" style="left:210px;top:180px">
    <p class="band-lead">Curabitur consequat mollis nulla Curabitur consequat lacinia.</p>
    <p class="band-body">Nullam cursus viverra elit, tristique ultrices metus porttitor vitae. Nunc tristique ac eros faucibus fermentum, sed auctor lorem.</p>
    <span class="outline-btn">CLICK HERE TO LEARN MORE</span>
  </div>
  <div class="abs mark-square" style="left:650px;top:180px"></div>
  <h2 class="abs band-title" style="left:820px;top:170px">OUR<br>MANTRA</h2>
</section>

<section class="band meet">
  <div class="band-photo" role="img" aria-label="Woman riding a bicycle past a blurred city street"></div>
  <div class="abs mark-square" style="left:76px;top:190px"></div>
  <h2 class="abs band-title" style="left:270px;top:150px;font-size:64px;line-height:70px">MEET<br>BRIGHT<br>SPARROW</h2>
  <div class="abs band-copy" style="left:740px;top:210px">
    <p class="band-lead">Curabitur consequat mollis nulla Curabitur consequat lacinia.</p>
    <p class="band-body">Nullam cursus viverra elit, tristique ultrices metus porttitor vitae. Nunc tristique ac eros faucibus fermentum, sed auctor lorem.</p>
    <span class="outline-btn">CLICK HERE TO LEARN MORE</span>
  </div>
</section>

<section class="band armor">
  <div class="band-photo" role="img" aria-label="Smiling woman in a white shirt sitting outdoors"></div>
  <div class="abs mark-square" style="left:650px;top:130px"></div>
  <h2 class="abs band-title" style="left:820px;top:120px">OUR<br>ARMOR</h2>
  <div class="abs band-copy" style="left:650px;top:310px">
    <p class="band-lead">Curabitur consequat mollis nulla Curabitur consequat lacinia.</p>
    <p class="band-body">Nullam cursus viverra elit, tristique ultrices metus porttitor vitae. Nunc tristique ac eros faucibus fermentum, sed auctor lorem.</p>
    <span class="outline-btn">SHOP NOW</span>
  </div>
</section>

<section class="showoff">
  <h2 class="abs showoff-title">SHOW OFF YOUR SUPER POWERS</h2>
  <p class="abs showoff-sub">Phasellus nisi felis, sagittis ac sapien in, pellentesque maximus odio.</p>
  <div class="social-row">
    <div class="social-tile">PAGEWAVE</div>
    <div class="social-tile">PICTOLANE</div>
  </div>
</section>

<section class="strip">
  <div class="strip-tile t1" role="img" aria-label="Featured woman standing on a city sidewalk"></div>
  <div class="strip-tile t2" role="img" aria-label="Featured woman in a wide hat outdoors"></div>
  <div class="strip-tile t3" role="img" aria-label="Featured woman in a jacket on a street"></div>
  <div class="strip-tile t4" role="img" aria-label="Featured woman posing against a light wall"></div>
  <div class="strip-tile t5" role="img" aria-label="Featured woman in a dark coat"></div>
  <div class="strip-tile t6" role="img" aria-label="Featured woman sitting in a green landscape"></div>
</section>

<section class="closing">
  <div class="fly">LET'S FLY <span class="fly-square"></span></div>
  <p class="abs closing-sub">Phasellus nisi felis, sagittis ac sapien in, pellentesque</p>
  <div class="signup">
    <div class="signup-field">Enter Your Email Address</div>
    <div class="signup-btn">LET'S FLY</div>
  </div>
</section>

<footer class="site-footer">
  <nav class="footer-nav"><span>MISSION</span><span>MANTRA</span><span>ARMOR</span><span>MEET BS</span></nav>
  <div class="footer-brand">
    <div class="brand-square"></div>
    <div class="brand-name">WE ARE<br>BRIGHT<br>SPARROW</div>
  </div>
  <p class="copyright">© 2024 We Are Bright Sparrow. All rights reserved.</p>
  <div class="page-marker">1</div>
</footer>

</body>
</html>
```